Personal development products that change your life

This is a direct selling business that sells personal development courses, but also sells the business as well if desired. This is not MLM, and there is no handling of the product required, nor hassling friends or family. We are looking for business minded people wanting to work their own hours and achieve a desirable income from this. A success image or happy image on a flyer would be great. I'd like the website address to be displayed as well thanks. www.grow-and-gain.com.au

Target Market(s)

Business-minded individuals searching for more finances. Self motivated, driven, interested in self development.

Industry/Entity Type

Business

Font styles to use
Sans Serif

Requirements
Must have
• Are you looking for
• - a franchise or business?
• - a change of career?
• - a back up income?
• Not MLM
• No product handling or shipping
• No hard sales required
• website: www.grow-and-gain.com.au
Nice to have
• A picture or background of excited person jumping in the air, or some similar.
• Worded to enrol people interested in achieving more financial headway, or flexible hours, or travel and do this business from anywhere in the world.
• Only need access to a phone, internet connection and a desire to succeed.

```html
<!DOCTYPE html>
<html lang="en">
<head>
<meta charset="utf-8">
<title>Personal Development Courses Flyer</title>
<link rel="stylesheet" href="https://fonts.googleapis.com/css2?family=Arimo:wght@700&family=Lato:ital,wght@0,300;0,400;0,700;0,900;1,400;1,700&family=Oswald:wght@400&display=swap">
<style>
  :root {
    --sky: #5b87c1;
    --sky-light: #77a0d2;
    --teal: #2a8aa2;
    --teal-bright: #3fb0d6;
    --navy: #1d3558;
    --navy-deep: #13284a;
    --paper: #eef0f2;
    --ink: #2b2f36;
    --mist: #8f969e;
    --white: #ffffff;
  }
  html, body {
    margin: 0;
    padding: 0;
    width: 904px;
    height: 1200px;
    overflow: hidden;
    background: var(--paper);
  }
  .flyer {
    position: relative;
    width: 904px;
    height: 1200px;
    overflow: hidden;
    font-family: "Lato", sans-serif;
  }
  .flyer-shapes {
    position: absolute;
    inset: 0;
    display: block;
  }
  .text {
    position: absolute;
    margin: 0;
    white-space: nowrap;
  }
  .title {
    left: 29px;
    top: 36px;
    font: italic 700 31px/38px "Lato", sans-serif;
    color: var(--white);
    text-shadow: 1px 2px 3px rgba(0,0,0,0.35);
  }
  .panel-kicker {
    left: 567px;
    width: 290px;
    top: 402px;
    text-align: center;
    font: 400 24px/30px "Oswald", sans-serif;
    color: var(--white);
  }
  .panel-headline {
    left: 567px;
    width: 290px;
    top: 448px;
    text-align: center;
    font: 700 25px/34px "Arimo", sans-serif;
    color: var(--white);
  }
  .panel-points {
    left: 590px;
    top: 532px;
    list-style: none;
    padding: 0;
    font: 700 18px/23px "Arimo", sans-serif;
    color: var(--white);
  }
  .panel-points li {
    position: relative;
    padding-left: 17px;
  }
  .panel-points li::before {
    content: "";
    position: absolute;
    left: 0;
    top: 7px;
    width: 9px;
    height: 9px;
    border-radius: 50%;
    background: var(--white);
  }
  .earnings {
    left: 27px;
    top: 540px;
    font: 400 37px/47px "Oswald", sans-serif;
    color: var(--teal);
  }
  .looking-for {
    left: 27px;
    top: 652px;
    font: 400 29px/36px "Oswald", sans-serif;
    color: var(--navy);
  }
  .options {
    left: 28px;
    top: 700px;
    list-style: none;
    padding: 0;
    font: italic 400 20px/38px "Lato", sans-serif;
    color: var(--ink);
  }
  .options li {
    display: flex;
    align-items: center;
    gap: 24px;
  }
  .options svg { display: block; }
  .seal-text {
    left: 382px;
    width: 120px;
    top: 668px;
    white-space: normal;
    text-align: center;
    font: italic 400 11.5px/15px "Lato", sans-serif;
    color: var(--white);
  }
  .balance {
    left: 27px;
    top: 818px;
    font: 900 27px/34px "Lato", sans-serif;
    color: var(--teal);
  }
  .balance-sub {
    left: 30px;
    top: 853px;
    font: 400 19px/24px "Lato", sans-serif;
    color: var(--ink);
  }
  .ongoing {
    left: 27px;
    top: 895px;
    font: 300 29px/37px "Lato", sans-serif;
    color: var(--mist);
  }
  .ongoing strong {
    display: block;
    font-weight: 700;
    color: var(--navy);
  }
  .ongoing span {
    display: block;
    font-size: 26px;
    line-height: 40px;
    font-weight: 400;
    color: var(--ink);
  }
  .requirements {
    left: 24px;
    top: 1098px;
    font: italic 700 17.5px/26px "Lato", sans-serif;
    color: var(--white);
  }
  .website {
    left: 24px;
    top: 1155px;
    font: 700 24px/30px "Lato", sans-serif;
    color: var(--teal-bright);
  }
</style>
</head>
<body>
<main class="flyer">
  <svg class="flyer-shapes" width="904" height="1200" viewBox="0 0 904 1200" aria-hidden="false">
    <defs>
      <linearGradient id="sky-fill" x1="0" y1="0" x2="0" y2="1">
        <stop offset="0" stop-color="#5a84bf"/>
        <stop offset="1" stop-color="#6e98cc"/>
      </linearGradient>
      <linearGradient id="faded-fill" x1="0" y1="0" x2="1" y2="1">
        <stop offset="0" stop-color="#e3e6e9"/>
        <stop offset="0.5" stop-color="#d3d7db"/>
        <stop offset="1" stop-color="#eceef0"/>
      </linearGradient>
      <linearGradient id="sky-photo-fill" x1="0" y1="0" x2="0" y2="1">
        <stop offset="0" stop-color="#3f7fd0"/>
        <stop offset="1" stop-color="#7eaee6"/>
      </linearGradient>
      <linearGradient id="snow-photo-fill" x1="0" y1="0" x2="0" y2="1">
        <stop offset="0" stop-color="#5e8fcf"/>
        <stop offset="0.6" stop-color="#b7cde6"/>
        <stop offset="1" stop-color="#8aa3c0"/>
      </linearGradient>
      <linearGradient id="band-fill" x1="0" y1="0" x2="1" y2="0">
        <stop offset="0" stop-color="#1a3a66"/>
        <stop offset="1" stop-color="#10254a"/>
      </linearGradient>
    </defs>

    <rect class="paper" width="904" height="1200" fill="var(--paper)"/>

    <polygon class="photo-faded" role="img" aria-label="Faded photo of a kitesurfer riding across the water"
      points="0,440 700,420 700,1090 0,1090" fill="url(#faded-fill)" opacity="0.85"/>

    <polygon class="photo-hero" role="img" aria-label="Photo of a young man leaping through the air between two boulders under a blue sky"
      points="0,0 904,0 904,332 310,492 0,410" fill="url(#sky-fill)"/>

    <polygon class="band-white" points="0,410 310,492 904,332 904,346 310,506 0,424" fill="var(--white)"/>
    <polygon class="band-teal" points="0,424 310,506 904,346 904,372 310,532 0,450" fill="var(--teal-bright)"/>
    <polygon class="band-navy" points="0,450 310,532 904,372 904,384 310,544 0,462" fill="var(--navy)"/>

    <polygon class="offer-panel" points="567,388 857,310 857,642 567,700" fill="var(--teal)"/>
    <polygon class="offer-panel-stripe" points="567,712 857,652 857,668 567,730" fill="var(--navy)"/>

    <polygon class="photo-paraglider" role="img" aria-label="Photo of a paraglider pilot in a red jacket flying against a blue sky"
      points="570,742 863,680 863,890 570,890" fill="url(#sky-photo-fill)"/>
    <polygon class="photo-skier" role="img" aria-label="Photo of a skier in a red jacket jumping above snowy mountains"
      points="570,906 863,906 863,1182 570,1142" fill="url(#snow-photo-fill)"/>

    <polygon class="footer-stripe" points="0,1064 260,1010 640,1100 640,1114 260,1024 0,1078" fill="var(--teal-bright)"/>
    <polygon class="footer-band" points="0,1080 260,1026 570,1100 570,1142 863,1182 904,1186 904,1200 0,1200" fill="url(#band-fill)"/>

    <g class="seal" transform="translate(442 718)">
      <polygon fill="var(--teal)" stroke="var(--white)" stroke-width="2"
        points="88,0 78,12.4 83.7,27.2 70.4,35.9 71.2,51.7 55.9,55.9 51.7,71.2 35.9,70.4 27.2,83.7 12.4,78 0,88 -12.4,78 -27.2,83.7 -35.9,70.4 -51.7,71.2 -55.9,55.9 -71.2,51.7 -70.4,35.9 -83.7,27.2 -78,12.4 -88,0 -78,-12.4 -83.7,-27.2 -70.4,-35.9 -71.2,-51.7 -55.9,-55.9 -51.7,-71.2 -35.9,-70.4 -27.2,-83.7 -12.4,-78 0,-88 12.4,-78 27.2,-83.7 35.9,-70.4 51.7,-71.2 55.9,-55.9 71.2,-51.7 70.4,-35.9 83.7,-27.2 78,-12.4"/>
    </g>
  </svg>

  <h1 class="text title">PERSONAL<br>DEVELOPMENT COURSES</h1>

  <p class="text panel-kicker">Earn up to $8000 per sale!</p>
  <p class="text panel-headline">Turn this into DOING<br>what YOU love!</p>
  <ul class="text panel-points">
    <li>Not MLM</li>
    <li>No product handling<br>or shipping</li>
    <li>No hard sales required</li>
  </ul>

  <p class="text earnings">Earn as little as $1800<br>or as much as $8000 per sale</p>
  <h2 class="text looking-for">ARE YOU LOOKING FOR</h2>
  <ul class="text options">
    <li><svg width="12" height="14" viewBox="0 0 12 14"><path d="M1 1 L8 7 L1 13" fill="none" stroke="var(--navy)" stroke-width="3.2"/></svg>A franchise or business?</li>
    <li><svg width="12" height="14" viewBox="0 0 12 14"><path d="M1 1 L8 7 L1 13" fill="none" stroke="var(--navy)" stroke-width="3.2"/></svg>A change of career?</li>
    <li><svg width="12" height="14" viewBox="0 0 12 14"><path d="M1 1 L8 7 L1 13" fill="none" stroke="var(--navy)" stroke-width="3.2"/></svg>A back up income?</li>
  </ul>

  <p class="text seal-text">To enrol people interested in achieving more financial headway, or flexible hours, or travel and do this business from anywhere in the world.</p>

  <p class="text balance">START THE WORK / LIFE BALANCE</p>
  <p class="text balance-sub">you've always wanted.</p>

  <p class="text ongoing">ONGOING PERSONAL<strong>DEVELOPMENT OPPORTUNITIES</strong><span>for successful applicants</span></p>

  <p class="text requirements">All you need is a laptop, a phone, a strong desire to succeed,<br>and dedicate 15-20 hours per week.</p>
  <p class="text website">www.grow-and-gain.com.au</p>
</main>
</body>
</html>
```